We need a complete design for our construction company KELTO CONSTRUCTION based in Auckland New Zealand, we need a logo, website, business card, vehicle design etc..
We are a mid to high-end construction company who work mostly on residential projects and some commercial.

What we want to see in the design;
Professional,
Architectural,
Simple,
Alternative,

We want the design to communicate professionalism, high quality wormanship and and quality service.

Target Market(s)

People looking for a quality building/ construction company

Industry/Entity Type

Construction Company

Contact Information for Business Card

KELTO CONSTRUCTION.co.nz
Lino Verasek
lino@keltoconstruction.example.nz
021 5807 462

Logo Text

KELTO CONSTRUCTION

Number of Pages Required

5+ page

Font styles to use
Sans Serif

Colors

Designer to choose colors to be used in the design.

Requirements
Must have
• Must appear high end, professional, quality, be simple, easy to use, give security to potential clients
Nice to have
• high-quality photos of our recent projects
• about us page
• blog page
• contact us page
• high quality content
Should not have
• should not be hard to use and have too much going on.

```html
<!DOCTYPE html>
<html lang="en">
<head>
<meta charset="utf-8">
<title>KELTO CONSTRUCTION</title>
<link href="https://fonts.googleapis.com/css2?family=Montserrat:wght@500;600;700&family=Open+Sans:wght@400;600&display=swap" rel="stylesheet">
<style>
:root{
  --red:#b3161b;
  --red-dark:#8f1014;
  --ink:#111111;
  --dark:#1c1c1c;
  --grey:#6f6f6f;
  --light:#efefef;
  --white:#ffffff;
}
*{margin:0;padding:0;box-sizing:border-box}
html,body{width:1200px;height:3905px;overflow:hidden}
body{font-family:"Open Sans",Arial,sans-serif;color:var(--ink);background:var(--white);position:relative}
section,header,footer{position:relative;width:1200px;overflow:hidden}
.abs{position:absolute}
h1,h2,h3,.btn,.nav a,.label{font-family:"Montserrat",Arial,sans-serif}
.btn{position:absolute;display:flex;align-items:center;justify-content:center;color:var(--white);font-weight:700;font-size:17px;letter-spacing:.5px;text-decoration:none}
.btn-red{background:var(--red)}
.btn-slant{clip-path:polygon(0 0,100% 0,95% 100%,0 100%)}

/* header */
.site-header{height:104px;background:var(--ink)}
.brand-panel{left:0;top:0;width:405px;height:104px;background:var(--white);clip-path:polygon(0 0,100% 0,84% 100%,0 100%)}
.brand{left:78px;top:20px;font-family:"Montserrat",sans-serif;font-weight:700;color:var(--red);display:flex;align-items:center;gap:10px}
.brand-mark{width:34px;height:34px;background:var(--red);flex:none}
.brand-name{display:flex;flex-direction:column;line-height:1}
.brand-name .big{font-size:40px;letter-spacing:1px}
.brand-name .small{font-size:12.5px;letter-spacing:6.3px;margin-top:4px}
.nav{left:435px;top:42px;display:flex;gap:33px}
.nav a{color:var(--white);font-size:15px;text-decoration:none;font-weight:500}
.nav a.active{color:var(--red)}
.estimate{left:898px;top:24px;width:225px;height:56px;font-size:16px}

/* hero */
.hero{height:573px;background:linear-gradient(115deg,#5b6776 0%,#9fb0c2 45%,#7a8b9b 70%,#3d4b3a 100%)}
.hero-overlay{inset:0;background:rgba(179,22,27,.85);clip-path:polygon(0 0,400px 0,700px 100%,0 100%)}
.hero h1{left:78px;top:146px;color:var(--white);font-size:58px;line-height:1.1;font-weight:700}
.hero p{left:78px;top:298px;width:520px;color:var(--white);font-size:15px;line-height:1.5}
.hero .btn{left:78px;top:396px;width:198px;height:50px;background:var(--ink);font-size:16px}
.dots{left:508px;top:514px;display:flex;gap:14px}
.dots span{width:30px;height:30px;border-radius:50%;border:3px solid var(--white);background:var(--ink)}
.dots span.on{background:var(--red)}

/* welcome */
.welcome{height:434px;text-align:center}
.eyebrow{left:0;right:0;top:62px;color:var(--red);font-size:19px;font-family:"Montserrat",sans-serif}
.welcome h2{left:0;right:0;top:94px;font-size:42px;font-weight:700}
.welcome .copy{left:180px;width:840px;font-size:13.5px;line-height:2;color:var(--grey)}
.welcome .btn{left:502px;top:320px;width:196px;height:48px}

/* about */
.about{height:521px;background:linear-gradient(90deg,#2a2a2a,#3a3936 50%,#262626)}
.person{left:78px;top:47px;width:404px;height:474px;background:linear-gradient(180deg,#c8b9a8,#8e8f93 60%,#6f7277)}
.about h2{left:510px;top:74px;color:var(--red);font-size:38px;font-weight:700}
.about p{left:510px;top:130px;width:620px;color:var(--white);font-size:14.5px;line-height:1.6}
.feature{width:240px;text-align:center;top:225px}
.feature .circle{width:124px;height:124px;border-radius:50%;background:var(--red);margin:0 auto;display:flex;align-items:center;justify-content:center}
.feature .label{color:var(--white);font-size:15px;line-height:1.5;margin-top:40px;font-weight:500}

/* call band */
.call{height:242px;background:var(--red);color:var(--white)}
.call h2{left:0;right:0;top:60px;text-align:center;font-size:29px;font-weight:700}
.call .lead{left:281px;top:142px;font-size:20px}
.phone-ring{left:556px;top:112px;width:86px;height:86px;border-radius:50%;border:3px solid var(--white);display:flex;align-items:center;justify-content:center}
.phone-ring span{width:64px;height:64px;border-radius:50%;background:var(--white);display:flex;align-items:center;justify-content:center}
.call .number{left:674px;top:142px;font-size:20px}

/* projects */
.projects{height:898px;text-align:center}
.projects h2{left:0;right:0;top:60px;font-size:40px;font-weight:700}
.projects .copy{left:220px;width:760px;top:128px;font-size:13.5px;line-height:2;color:var(--grey)}
.filter{top:196px;height:52px;border:2px solid #cfcfcf;font-size:15px;color:var(--grey);background:var(--white);display:flex;align-items:center;justify-content:center;font-family:"Montserrat",sans-serif;clip-path:polygon(5% 0,100% 0,95% 100%,0 100%)}
.filter.on{background:var(--red);color:var(--white);border-color:var(--red)}
.tile{width:336px;height:227px}
.tile.hover::after{content:"";position:absolute;inset:0;background:rgba(179,22,27,.82)}
.tile.hover .frame{position:absolute;inset:16px;border:2px solid rgba(255,255,255,.6);z-index:1}
.tile.hover svg{position:absolute;left:148px;top:94px;z-index:2}
.projects .btn{left:502px;top:781px;width:196px;height:48px}

/* blog */
.blog{height:378px;background:var(--light)}
.blog h2{left:0;right:0;top:56px;text-align:center;font-size:38px;font-weight:700}
.post-img{top:143px;width:216px;height:165px}
.post{top:138px;width:270px}
.post h3{font-size:16px;line-height:1.5;font-weight:700}
.post .date{color:var(--red);font-size:14px;font-weight:600;margin:8px 0 6px;display:flex;align-items:center;gap:7px}
.post p{font-size:13px;line-height:2;color:var(--grey)}
.post p b{color:var(--red)}

/* contact */
.contact{height:624px;background:linear-gradient(180deg,#232323,#2e2e2e 50%,#1e1e1e);color:var(--white)}
.contact h2{left:0;right:0;top:56px;text-align:center;font-size:40px;font-weight:600}
.contact h3{top:148px;font-size:24px;font-weight:500;text-align:center;width:300px}
.field{left:78px;width:497px;height:53px;background:var(--white);color:#777;font-size:13px;padding:16px 18px}
.field.msg{height:135px}
.send{left:266px;top:458px;width:124px;height:124px;border-radius:50%;background:var(--red);display:flex;align-items:center;justify-content:center;font-family:"Montserrat",sans-serif;font-weight:700;font-size:19px}
.info{left:724px;font-size:14px;line-height:1.8;display:flex;gap:14px;align-items:flex-start}
.info svg{flex:none;margin-top:4px}
.social{top:596px;width:40px;height:40px;border-radius:50%;background:var(--red)}

/* footer */
.site-footer{height:131px;background:var(--red);color:var(--white);text-align:center;font-size:13px}
.notch{left:545px;top:-52px;width:110px;height:52px;background:var(--red);clip-path:polygon(50% 0,100% 100%,0 100%)}
.foot-links{left:0;right:0;top:42px}
.copyright{left:0;right:0;top:72px}
</style>
</head>
<body>

<header class="site-header">
  <div class="abs brand-panel"></div>
  <div class="abs brand"><span class="brand-mark"></span><span class="brand-name"><span class="big">KELTO</span><span class="small">CONSTRUCTION</span></span></div>
  <nav class="abs nav">
    <a class="active" href="#">HOME ▾</a><a href="#">ABOUT</a><a href="#">PROJECTS</a><a href="#">BLOG</a><a href="#">CONTACT</a>
  </nav>
  <a class="btn btn-red estimate" href="#">GET FREE ESTIMATE</a>
</header>

<section class="hero" role="img" aria-label="Photo of a modern glass-fronted two-storey house at dusk">
  <div class="abs hero-overlay"></div>
  <h1 class="abs">KELTO<br>CONSTRUCTION</h1>
  <p class="abs">Lorem Ipsum is simply dummy text of the printing and typesetting industry. Lorem Ipsum has been the industry's standard dummy text ever since the.</p>
  <a class="btn btn-slant" href="#">CONTACT US</a>
  <div class="abs dots"><span class="on"></span><span></span><span></span><span></span></div>
</section>

<section class="welcome">
  <div class="abs eyebrow">WELCOME TO</div>
  <h2 class="abs">KELTO CONSTRUCTION</h2>
  <p class="abs copy" style="top:150px">Lorem Ipsum is simply dummy text of the printing and typesetting industry. Lorem Ipsum has been the industry's standard dummy text ever since the when an unknown printer took a galley of type and scrambled it to make.</p>
  <p class="abs copy" style="top:220px">Lorem Ipsum is simply dummy text of the printing and typesetting industry. Lorem Ipsum has been the industry's standard dummy text ever since the 1500s, when an unknown printer took a galley of type and scrambled it to make a type specimen book. It has survived not only five centuries, but also the leap into electronic typesetting, remaining essentially unchanged.</p>
  <a class="btn btn-red btn-slant" href="#">LEARN MORE</a>
</section>

<section class="about" role="img" aria-label="Dark photo of a city construction site with cranes">
  <div class="abs person" role="img" aria-label="Photo of a smiling builder in a grey shirt with arms crossed"></div>
  <h2 class="abs">ABOUT US</h2>
  <p class="abs">Lorem Ipsum is simply dummy text of the printing and typesetting industry. Lorem Ipsum has been the industry's standard dummy text ever since the.</p>
  <div class="abs feature" style="left:440px">
    <div class="circle"><svg width="60" height="60" viewBox="0 0 60 60" fill="none" stroke="#fff" stroke-width="3"><circle cx="20" cy="18" r="7"/><circle cx="40" cy="18" r="7"/><path d="M8 48v-8a10 10 0 0 1 20 0v8M32 48v-8a10 10 0 0 1 20 0v8"/></svg></div>
    <div class="label">COMMUNICATE<br>PROFESSIONALISM</div>
  </div>
  <div class="abs feature" style="left:687px">
    <div class="circle"><svg width="60" height="60" viewBox="0 0 60 60" fill="none" stroke="#fff" stroke-width="3"><circle cx="30" cy="24" r="14"/><path d="M22 36l-5 16 13-6 13 6-5-16"/><path d="M24 24l4 4 8-8"/></svg></div>
    <div class="label">HIGH QUALITY<br>WORMANSHIP</div>
  </div>
  <div class="abs feature" style="left:908px">
    <div class="circle"><svg width="60" height="60" viewBox="0 0 60 60" fill="none" stroke="#fff" stroke-width="3"><rect x="16" y="10" width="28" height="38"/><path d="M22 20h16M22 28h16M22 36h10"/></svg></div>
    <div class="label">QUALITY<br>SERVICE</div>
  </div>
</section>

<section class="call">
  <h2 class="abs">IF YOU NEED RESIDENTIAL AND OMMERCIAL CONSTRUCTION</h2>
  <div class="abs lead">Please Contact Us On</div>
  <div class="abs phone-ring"><span><svg width="32" height="32" viewBox="0 0 24 24"><path fill="#b3161b" d="M6.6 10.8a15 15 0 0 0 6.6 6.6l2.2-2.2c.3-.3.7-.4 1-.2 1.1.4 2.3.6 3.6.6.6 0 1 .4 1 1V20c0 .6-.4 1-1 1A17 17 0 0 1 3 4c0-.6.4-1 1-1h3.5c.6 0 1 .4 1 1 0 1.3.2 2.5.6 3.6.1.3 0 .7-.2 1z"/></svg></span></div>
  <div class="abs number">+1 123 456 7890</div>
</section>

<section class="projects">
  <h2 class="abs">OUR PROJECTS</h2>
  <p class="abs copy">Lorem Ipsum is simply dummy text of the printing and typesetting industry. Lorem Ipsum has been the industry's standard dummy text ever since the when an unknown printer took.</p>
  <div class="abs filter on" style="left:377px;width:94px">ALL</div>
  <div class="abs filter" style="left:484px;width:154px">COMMERCIAL</div>
  <div class="abs filter" style="left:646px;width:177px">RESIDENTIAL</div>

  <div class="abs tile hover" style="left:78px;top:281px;background:linear-gradient(180deg,#b9a08e,#7d6a5e)" role="img" aria-label="Photo of a brick commercial building">
    <span class="frame"></span>
    <svg width="40" height="40" viewBox="0 0 40 40" fill="none" stroke="#fff" stroke-width="3"><circle cx="17" cy="17" r="12"/><path d="M26 26l10 10M17 11v12M11 17h12"/></svg>
  </div>
  <div class="abs tile" style="left:432px;top:281px;background:linear-gradient(180deg,#e6eef4,#c8b49c 55%,#7a8a5a)" role="img" aria-label="Photo of a Mediterranean style house with tiled roof"></div>
  <div class="abs tile" style="left:789px;top:281px;background:linear-gradient(160deg,#3f73b5,#b88b4e 55%,#c8d24a)" role="img" aria-label="Photo of workers in hard hats on a building site"></div>
  <div class="abs tile" style="left:78px;top:534px;background:linear-gradient(180deg,#8aa6c8,#5d5e60 60%,#3e4a35)" role="img" aria-label="Photo of a modern glass house"></div>
  <div class="abs tile" style="left:432px;top:534px;background:linear-gradient(180deg,#6f86a8,#c9c9c6 55%,#4a4a48)" role="img" aria-label="Photo of a white contemporary house at dusk"></div>
  <div class="abs tile" style="left:789px;top:534px;background:linear-gradient(180deg,#8fb0d8,#c9c1b4 55%,#5c6a45)" role="img" aria-label="Photo of a two-storey family home"></div>
  <a class="btn btn-red btn-slant" href="#">SUBMIT</a>
</section>

<section class="blog">
  <h2 class="abs">LATEST BLOG POST</h2>
  <div class="abs post-img" style="left:78px;background:linear-gradient(180deg,#e9eef3,#d2c49a 70%,#e8c24a)" role="img" aria-label="Photo of builders reviewing plans with a hard hat"></div>
  <div class="abs post" style="left:312px">
    <h3>Lorem Ipsum is the simply Text dummy text of the print.</h3>
    <div class="date"><svg width="14" height="14" viewBox="0 0 14 14"><rect x="1" y="2" width="12" height="11" fill="#b3161b"/><rect x="2.5" y="5" width="9" height="6.5" fill="#fff"/></svg>19 March 2018</div>
    <p>Lorem Ipsum is simply dummy text of the printing and typesetting industry. Lorem Ipsum has been..<b>»</b></p>
  </div>
  <div class="abs post-img" style="left:635px;background:linear-gradient(180deg,#a9bcd0,#6d7680 55%,#c7d23a)" role="img" aria-label="Photo of a site worker in a hi-vis vest overlooking a city"></div>
  <div class="abs post" style="left:867px">
    <h3>Lorem Ipsum is the simply Text dummy text of the print.</h3>
    <div class="date"><svg width="14" height="14" viewBox="0 0 14 14"><rect x="1" y="2" width="12" height="11" fill="#b3161b"/><rect x="2.5" y="5" width="9" height="6.5" fill="#fff"/></svg>19 March 2018</div>
    <p>Lorem Ipsum is simply dummy text of the printing and typesetting industry. Lorem Ipsum has been..<b>»</b></p>
  </div>
</section>

<section class="contact" role="img" aria-label="Dark photo of a city skyline">
  <h2 class="abs">CONTACT US</h2>
  <h3 class="abs" style="left:176px">INQUIRY FORM</h3>
  <h3 class="abs" style="left:722px">KEEP IN TOUCH</h3>
  <div class="abs field" style="top:197px">Enter Name :</div>
  <div class="abs field" style="top:259px">Enter Phone No :</div>
  <div class="abs field" style="top:321px">Enter E-Mail :</div>
  <div class="abs field msg" style="top:385px">Message :</div>
  <div class="abs send">SUBMIT</div>

  <div class="abs info" style="top:212px">
    <svg width="22" height="18" viewBox="0 0 22 18"><path fill="#b3161b" d="M11 0l11 8h-3v10H3V8H0z"/></svg>
    <div>KELTO CONSTRUCTION<br><span style="font-size:13px">101 - lorem ipsum is simple dummy text<br>of print and type setting<br>print of industry</span></div>
  </div>
  <div class="abs info" style="top:344px">
    <svg width="20" height="14" viewBox="0 0 20 14"><rect width="20" height="14" fill="#b3161b"/><path d="M0 0l10 8 10-8" fill="none" stroke="#fff" stroke-width="1.5"/></svg>
    <div>info@kelto.example.com</div>
  </div>
  <div class="abs info" style="top:397px">
    <svg width="18" height="18" viewBox="0 0 24 24"><path fill="#b3161b" d="M6.6 10.8a15 15 0 0 0 6.6 6.6l2.2-2.2c.3-.3.7-.4 1-.2 1.1.4 2.3.6 3.6.6.6 0 1 .4 1 1V20c0 .6-.4 1-1 1A17 17 0 0 1 3 4c0-.6.4-1 1-1h3.5c.6 0 1 .4 1 1 0 1.3.2 2.5.6 3.6.1.3 0 .7-.2 1z"/></svg>
    <div>+1 123 456 7890</div>
  </div>
  <div class="abs social" style="left:727px;top:446px"></div>
  <div class="abs social" style="left:779px;top:446px"></div>
  <div class="abs social" style="left:831px;top:446px"></div>
</section>

<footer class="site-footer" style="overflow:visible">
  <div class="abs notch"></div>
  <svg class="abs" style="left:584px;top:-38px" width="32" height="26" viewBox="0 0 32 26" fill="none" stroke="#fff" stroke-width="3"><path d="M4 14l12-10 12 10M4 24l12-10 12 10"/></svg>
  <div class="abs foot-links">Home &nbsp;|&nbsp; About &nbsp;|&nbsp; Projects &nbsp;|&nbsp; Blog &nbsp;|&nbsp; Contact</div>
  <div class="abs copyright">©KELTO CONSTRUCTION - 2018 All Right Reserved.</div>
</footer>

</body>
</html>
```